indépendant en tant que Massothérapeute et Préparateur Mental, j'ai besoin de ...

Massothérapeute et préparateur mental indépendant, je recherche une carte de visite sobre et dynamique, sans images liées au massage ou à la préparation mentale mais intégrant mon logo. Les couleurs que j'aime bien sont : Blanc, gris, anthracite, noir et jaune

Contact Information for Business Card

carte de préférence Horizontale
neutre qui puisse toucher le deux domaines Massothérapie et préparation mentale

Requirements
Must have
• mon projet doit intégrer au recto:
LOGO
Loïc Bardèze
078 513 26 48
info@loicbardeze.ch
et éventuellement www.loicbardeze.ch

et au verso les deux adresses:

Chemin des Ormilles 7B
1400 Yverdon-les-Bains

Route de la Gravière 9
1700 Fribourg

Should not have
• mon projet ne doit pas contenir d'image en liens avec le massage ni la préparation mentale.

```html
<!DOCTYPE html>
<html lang="fr">
<head>
<meta charset="utf-8">
<title>Loïc Bardèze – Cartes de visite</title>
<link rel="stylesheet" href="https://fonts.googleapis.com/css2?family=Roboto:wght@400;500;700;900&display=swap">
<style>
  :root {
    --backdrop: #3a3330;
    --anthracite: #2d2d30;
    --paper: #ffffff;
    --ink: #1c1c1e;
    --grey-text: #b9b9bc;
    --faint: #e3e3e5;
    --accent: #f2b705;
  }
  * { box-sizing: border-box; margin: 0; padding: 0; }
  html, body {
    width: 1200px; height: 795px; overflow: hidden;
    background: var(--backdrop);
    font-family: "Roboto", Arial, sans-serif;
  }
  .stage {
    position: relative; width: 1200px; height: 795px;
  }
  .card {
    position: absolute; top: 230px;
    width: 520px; height: 336px;
    box-shadow: 0 10px 24px rgba(0,0,0,.35);
    overflow: hidden;
  }
  .card--back { left: 50px; background: var(--anthracite); }
  .card--front { left: 630px; background: var(--paper); }

  .brand { position: absolute; display: flex; align-items: center; gap: 10px; }
  .brand__dot { width: 14px; height: 14px; border-radius: 50%; background: var(--accent); }
  .brand__name { font-weight: 700; font-size: 30px; letter-spacing: .5px; text-transform: uppercase; }
  .brand__tagline {
    position: absolute; font-size: 9px; letter-spacing: 1.2px; text-transform: uppercase;
  }
  .card--back .brand { left: 150px; top: 110px; }
  .card--back .brand__name { color: #111113; }
  .card--back .brand__tagline { left: 174px; top: 152px; color: #111113; }

  .addresses { position: absolute; left: 44px; top: 210px; list-style: none; }
  .addresses li {
    display: flex; align-items: center; gap: 8px;
    color: var(--grey-text); font-size: 15px; margin-bottom: 10px;
  }
  .addresses li:nth-child(2) { padding-left: 24px; }

  .card--front .brand { left: 160px; top: 40px; }
  .card--front .brand__name { color: var(--ink); }
  .card--front .brand__tagline { left: 184px; top: 82px; color: var(--ink); }

  .holder { position: absolute; left: 40px; top: 120px; color: var(--ink); }
  .holder__name { font-weight: 700; font-size: 21px; text-transform: uppercase; }
  .holder__role { font-size: 16px; margin-top: 2px; }

  .contacts { position: absolute; left: 40px; top: 195px; list-style: none; }
  .contacts li {
    display: flex; align-items: center; gap: 8px;
    font-size: 16px; color: var(--ink); margin-bottom: 6px;
  }
  .icon { width: 12px; height: 12px; flex: none; }

  .watermark-name {
    position: absolute; right: 20px; bottom: 22px;
    font-weight: 700; font-size: 50px; color: var(--faint);
    text-transform: uppercase; letter-spacing: 1px;
  }
</style>
</head>
<body>
<main class="stage">

  <section class="card card--back" aria-label="Verso">
    <div class="brand">
      <span class="brand__dot"></span>
      <span class="brand__name">Loïc Bardèze</span>
    </div>
    <p class="brand__tagline">Massothérapeute / Préparateur mental</p>
    <ul class="addresses">
      <li>
        <svg class="icon" viewBox="0 0 12 12" aria-hidden="true"><path d="M6 0a4 4 0 0 0-4 4c0 3 4 8 4 8s4-5 4-8a4 4 0 0 0-4-4z" fill="var(--accent)"/><circle cx="6" cy="4" r="1.5" fill="var(--anthracite)"/></svg>
        Chemin des Ormilles 7B, 1400 Yverdon-les-Bains
      </li>
      <li>
        <svg class="icon" viewBox="0 0 12 12" aria-hidden="true"><path d="M6 0a4 4 0 0 0-4 4c0 3 4 8 4 8s4-5 4-8a4 4 0 0 0-4-4z" fill="var(--accent)"/><circle cx="6" cy="4" r="1.5" fill="var(--anthracite)"/></svg>
        Route de la Gravière 9, 1700 Fribourg
      </li>
    </ul>
  </section>

  <section class="card card--front" aria-label="Recto">
    <div class="brand">
      <span class="brand__dot"></span>
      <span class="brand__name">Loïc Bardèze</span>
    </div>
    <p class="brand__tagline">Massothérapeute / Préparateur mental</p>

    <div class="holder">
      <p class="holder__name">Loïc Bardèze</p>
      <p class="holder__role">Founder &amp; CEO</p>
    </div>

    <ul class="contacts">
      <li>
        <svg class="icon" viewBox="0 0 12 12" aria-hidden="true"><path d="M2 1l2 0 1 3-1.5 1a6 6 0 0 0 3.5 3.5L8 7l3 1v2a1 1 0 0 1-1 1A9 9 0 0 1 1 2a1 1 0 0 1 1-1z" fill="var(--accent)"/></svg>
        078 513 26 48
      </li>
      <li>
        <svg class="icon" viewBox="0 0 12 12" aria-hidden="true"><rect x="0.5" y="2" width="11" height="8" fill="var(--accent)"/><path d="M0.5 2l5.5 4.5L11.5 2" fill="none" stroke="#fff" stroke-width="1"/></svg>
        info@loicbardeze.ch
      </li>
      <li>
        <svg class="icon" viewBox="0 0 12 12" aria-hidden="true"><circle cx="6" cy="6" r="5.5" fill="var(--accent)"/><path d="M0.5 6h11M6 0.5c-2 2-2 9 0 11M6 0.5c2 2 2 9 0 11" fill="none" stroke="#fff" stroke-width=".8"/></svg>
        www.loicbardeze.ch
      </li>
    </ul>

    <p class="watermark-name" aria-hidden="true">Bardèze</p>
  </section>

</main>
</body>
</html>
```